Creative, fresh business card design for Ripplecraft Facades

We need a fresh, creative business card design for Ripplecraft Facades. We are the manufacturer of Ripplecraft Facades in Australia. Wall panels are 2400 x 1200mm panels made from MDF and feature 3D patterns on the face of the panel. The colours to be used are green, silver/grey and white RGB
Red 187
Green 207
Blue 65.

An idea is to possibly use a watermark of one of our designs as a background (like on the "Grids" design on the left hand side of page 2 of our brochure).

Target Market(s)

Interior designers, architects, builders and home renovators

Industry/Entity Type

Business

Contact Information for Business Card

Details to go on the card are:
Our logo (attached),
Slogan: "Decorative panels for interiors and exteriors",
Contact name,
Position,
Mobile phone number,
Business address,
Business phone,
Business fax,
Website and
Email address.

I have attached a few images of our panels and our brochure for reference.

The colours of the business card should feature our logo colours which are: RGB
Red 187
Green 207
Blue 65

Requirements
Must have
• Very modern fonts and design. Some of the designs shown especially the "Prisms" design which is a popular design.
Nice to have
• Creative but simple design. Very contemporary.
Should not have
• Anything ornate or old fashioned.

```html
<!DOCTYPE html>
<html lang="en">
<head>
<meta charset="utf-8">
<title>Ripplecraft Facades – Business Card</title>
<link href="https://fonts.googleapis.com/css2?family=Cormorant+Garamond:wght@500&family=Open+Sans:wght@400;600&display=swap" rel="stylesheet">
<style>
  :root {
    --stage: #2e2d2f;
    --card: #f1f0ec;
    --card-light: #faf9f6;
    --card-shade: #e2e0da;
    --brand-green: rgb(187, 207, 65);
    --ink: #3b3b3d;
    --rule: #6a6a6c;
  }
  html, body {
    margin: 0;
    width: 1200px;
    height: 1000px;
    overflow: hidden;
    background: var(--stage);
  }
  .business-card {
    position: absolute;
    left: 230px;
    top: 290px;
    width: 740px;
    height: 420px;
    background: var(--card);
    overflow: hidden;
  }
  .card-texture {
    position: absolute;
    inset: 0;
    background: linear-gradient(172deg, var(--card-light) 0%, var(--card) 45%, var(--card-shade) 100%);
  }
  .brand-block {
    position: absolute;
    left: 100px;
    top: 92px;
    width: 220px;
  }
  .brand-name {
    display: flex;
    align-items: center;
    gap: 10px;
    font-family: "Open Sans", sans-serif;
    font-weight: 600;
    font-size: 24px;
    line-height: 1.15;
    color: var(--brand-green);
  }
  .brand-mark {
    flex: none;
    width: 22px;
    height: 22px;
    background: var(--brand-green);
  }
  .brand-slogan {
    margin: 44px 0 0;
    font-family: "Cormorant Garamond", serif;
    font-weight: 500;
    font-size: 21px;
    line-height: 1.05;
    color: var(--ink);
  }
  .card-divider {
    position: absolute;
    left: 346px;
    top: 86px;
    width: 2px;
    height: 192px;
    background: var(--rule);
  }
  .contact-list {
    position: absolute;
    left: 370px;
    top: 88px;
    margin: 0;
    padding: 0;
    list-style: none;
    font-family: "Open Sans", sans-serif;
    font-size: 15px;
    line-height: 23px;
    color: var(--ink);
  }
  .contact-name {
    font-weight: 600;
  }
  .contact-role {
    margin-bottom: 8px;
  }
</style>
</head>
<body>
  <article class="business-card">
    <div class="card-texture" role="img" aria-label="Soft white relief of flowing wave wall panels as card background"></div>
    <div class="brand-block">
      <div class="brand-name"><span class="brand-mark"></span>Ripplecraft Facades</div>
      <p class="brand-slogan">decorative panels for<br>interiors &amp; exteriors</p>
    </div>
    <div class="card-divider"></div>
    <ul class="contact-list">
      <li class="contact-name">Daniel Mercer</li>
      <li class="contact-role">Sales Manager</li>
      <li>Mobile: 0400 555 219</li>
      <li>Telephone: 02 5550 3180</li>
      <li>Business fax: 02 5550 3181</li>
      <li>14 Tidewater Road, Eastwood Vale NSW 2199</li>
      <li>www.ripplecraftfacades.com.au</li>
      <li>sales@ripplecraftfacades.com.au</li>
    </ul>
  </article>
</body>
</html>
```